Harrow Point Metrics Company Website Design and Coding

We want to redesign our existing website so that it is more visually and functionally appealing to prospective clients and potential job candidates. We would like to keep our current color scheme and implement our current logo as well. We have a high-level idea of website structure that we are thinking of, which is in the attached files. Logo is included as well. The final design would ideally be energy and analytics focused. We will need the new website to be coded as well, please.

Target Market(s)

Energy and utility industry

Industry/Entity Type

Energy/analytics

Coding

Coded - Design and coding required

Number of Pages Required

5+ page

Font styles to use
Sans Serif

Colors
0094D4
00A9DD
6FCCEA
C7EBF8
E9F6FB
F0912C
F2A743
F7CA91
FBE8D2
FDF5EE

Requirements
Must have
• Consistent color scheme- please use the one that we provided. We need an overview, a home page, and our core services. A separate job application page. Logo must be incorporated. We would like e "Meet our Team" page. Please include all of the content that is listed in our attachments.
Nice to have
• Movement
Should not have
• No music, no cartoons/animation, no pictures of a chalkboard

```html
<!DOCTYPE html>
<html lang="en">
<head>
<meta charset="utf-8">
<title>Harrow Point Metrics</title>
<link href="https://fonts.googleapis.com/css2?family=Open+Sans:wght@400;500;600;700;800&family=Oswald:wght@300;400&display=swap" rel="stylesheet">
<style>
:root{
  --blue:#1a9ad6;
  --blue-dark:#0094d4;
  --navy:#1f2a5e;
  --navy-deep:#18204d;
  --orange:#e8692a;
  --card:#f3f3f3;
  --ink:#111;
  --text:#444;
  --purple:#8a80b2;
  --white:#fff;
}
*{box-sizing:border-box;margin:0;padding:0}
html,body{width:1200px;height:2613px;overflow:hidden}
body{font-family:"Open Sans",sans-serif;color:var(--ink);background:var(--white);position:relative}
a{color:inherit;text-decoration:none}

.brand{position:absolute;display:flex;align-items:center;gap:10px}
.brand-dot{width:34px;height:34px;border-radius:50%;background:var(--blue)}
.brand-name{font-size:21px;font-weight:500;color:var(--blue);letter-spacing:-.2px}

.top-nav{position:absolute;display:flex;gap:35px;font-size:17px;color:#222}

.site-header{position:absolute;top:0;left:0;width:1200px;height:80px;background:var(--white)}
.sub-nav{position:absolute;top:80px;left:0;width:1200px;height:48px;background:var(--blue);
  font-family:"Oswald",sans-serif;font-weight:300;font-size:14px;color:var(--white)}
.sub-nav ul{list-style:none;display:flex;gap:18px;position:absolute;left:108px;top:13px}
.sub-nav li.active{border-bottom:2px solid var(--white);padding-bottom:10px}

.hero{position:absolute;top:128px;left:0;width:1200px;height:600px;
  background:linear-gradient(100deg,var(--navy) 0%,var(--navy) 55%,var(--navy-deep) 100%);overflow:hidden}
.hero-art{position:absolute;left:660px;top:50px;width:540px;height:550px;
  background:radial-gradient(ellipse at 55% 60%,#3a6fe0 0%,#2b3d9a 35%,#1e2a6a 65%,rgba(31,42,94,0) 80%)}
.hero h1{position:absolute;left:100px;top:100px;color:var(--white);font-size:50px;font-weight:500;line-height:60px}
.hero h1 strong{display:block;font-weight:700;letter-spacing:.5px}
.hero .lead{position:absolute;left:97px;top:252px;width:600px;color:var(--white);
  font-size:21.5px;font-weight:700;line-height:28.5px;text-transform:uppercase}
.btn{display:inline-flex;align-items:center;justify-content:center;background:var(--orange);color:var(--white);border-radius:30px;font-weight:500}
.hero .btn{position:absolute;left:101px;top:392px;width:180px;height:53px;font-size:22px}

.section-title{position:absolute;left:0;width:1200px;text-align:center;font-weight:700;text-transform:uppercase}
.services-title{top:865px;font-size:44px;color:var(--blue)}

.service{position:absolute;width:318px;height:283px;background:var(--card);border-radius:14px;
  border-left:9px solid var(--blue);padding:68px 10px 0 16px}
.service.highlight{border-left-color:var(--orange)}
.service h3{font-size:17.5px;font-weight:700;line-height:24px;text-transform:uppercase;letter-spacing:0;min-height:55px}
.service p{font-size:14.5px;line-height:21.5px;color:var(--text);letter-spacing:-.15px}
.service .more{position:absolute;left:18px;bottom:28px;font-size:17px;font-weight:500}
.service.highlight .more{left:14px;bottom:14px;height:40px;padding:0 16px;font-size:17px}
.service .icon{position:absolute;left:10px;top:-30px}
.service .icon-badge{position:absolute;left:-2px;top:-33px;width:88px;height:88px;border-radius:50%;background:var(--orange);
  display:flex;align-items:center;justify-content:center}

.cases-band{position:absolute;top:1715px;left:0;width:1200px;height:322px;background:var(--purple)}
.cases-title{top:1825px;font-size:40px;color:var(--white)}
.case{position:absolute;top:1926px;width:493px;height:366px;background:var(--white);border:2px solid #ddd;border-radius:6px}
.case-media{position:absolute;left:9px;top:8px;width:473px;height:200px}
.case h3{position:absolute;left:22px;top:207px;width:450px;font-size:22px;line-height:28px;font-weight:700;text-transform:uppercase;letter-spacing:.3px}
.case .btn{position:absolute;left:20px;top:299px;width:154px;height:53px;font-size:22px}
.view-all{position:absolute;left:484px;top:2348px;width:233px;height:62px;border:2px solid var(--orange);border-radius:32px;
  display:flex;align-items:center;justify-content:center;font-size:17px;font-weight:600}

.site-footer .rule{position:absolute;left:98px;top:2468px;width:1014px;height:1px;background:var(--blue)}
.copyright{position:absolute;top:2572px;left:0;width:1200px;text-align:center;font-size:13px;color:#333}
</style>
</head>
<body>

<header class="site-header">
  <a class="brand" style="left:100px;top:22px"><span class="brand-dot"></span><span class="brand-name">Harrow Point Metrics</span></a>
  <nav class="top-nav" style="left:533px;top:31px">
    <a>Home</a><a>Core Services</a><a>About</a><a>Our Work</a><a>Blog</a><a>Contact Us</a>
  </nav>
</header>

<nav class="sub-nav">
  <ul>
    <li class="active">Forecating &amp; Perdictive Analytics</li>
    <li>T&amp;D Planning</li>
    <li>Evaluation</li>
    <li>Pilot&amp; Emerging Tech Support</li>
    <li>Program &amp; Portfolio Resource Planning</li>
    <li>Program &amp; Delivery Support</li>
    <li>Company overview</li>
    <li>More</li>
  </ul>
</nav>

<section class="hero">
  <div class="hero-art" role="img" aria-label="Illustration of a laptop with analytics dashboard floating above a ring of glowing blue particles"></div>
  <h1>Welcome to<strong>HARROW POINT METRICS</strong></h1>
  <p class="lead">Harrow Point Metrics is a consulting company that helps utilities and regulatory agencies navigate the challenges of building a smarter and cleaner energy future.</p>
  <a class="btn">Get Started</a>
</section>

<h2 class="section-title services-title">Our Services</h2>

<article class="service" style="left:100px;top:1010px">
  <svg class="icon" width="66" height="64" viewBox="0 0 66 64" fill="none" stroke="#111" stroke-width="2"><rect x="2" y="22" width="8" height="26"/><rect x="14" y="14" width="8" height="34"/><rect x="26" y="8" width="8" height="16"/><polyline points="4,14 16,6 28,10 44,2"/><circle cx="40" cy="40" r="14"/><line x1="50" y1="50" x2="62" y2="62"/><text x="35" y="46" font-size="16" fill="#111" stroke="none">$</text></svg>
  <h3>Predictive Analytics and Forecasting</h3>
  <p>Lorem ipsum dolor sit amet, consectetur adipiscing elit, sed do eiusmod tempor incididunt ut labore et dolore magna aliqua.</p>
  <a class="more">Read More</a>
</article>

<article class="service highlight" style="left:440px;top:1010px">
  <div class="icon-badge"><svg width="50" height="50" viewBox="0 0 50 50" fill="none" stroke="#fff" stroke-width="2"><circle cx="18" cy="14" r="7"/><circle cx="18" cy="14" r="3"/><rect x="30" y="4" width="8" height="8"/><rect x="30" y="18" width="8" height="8"/><path d="M4 36h10l8 4h10l10-6v6l-12 8H14l-10-4"/></svg></div>
  <h3>T&amp;D Planning</h3>
  <p>Lorem ipsum dolor sit amet, consectetur adipiscing elit, sed do eiusmod tempor incididunt ut labore et dolore magna aliqua.</p>
  <a class="more btn">Read More</a>
</article>

<article class="service" style="left:779px;top:1010px">
  <svg class="icon" width="50" height="58" viewBox="0 0 50 58" fill="none" stroke="#111" stroke-width="2"><rect x="3" y="2" width="36" height="52"/><rect x="9" y="10" width="7" height="7"/><rect x="9" y="24" width="7" height="7"/><rect x="9" y="38" width="7" height="7"/><line x1="20" y1="13" x2="34" y2="13"/><line x1="20" y1="27" x2="34" y2="27"/><line x1="20" y1="41" x2="30" y2="41"/><line x1="46" y1="22" x2="34" y2="54"/></svg>
  <h3>Evaluation</h3>
  <p>Lorem ipsum dolor sit amet, consectetur adipiscing elit, sed do eiusmod tempor incididunt ut labore et dolore magna aliqua.</p>
  <a class="more">Read More</a>
</article>

<article class="service" style="left:100px;top:1390px">
  <svg class="icon" width="92" height="40" viewBox="0 0 92 40" fill="none" stroke="#111" stroke-width="2" style="left:6px;top:-24px"><circle cx="46" cy="20" r="16"/><polygon points="46,10 49,17 56,17 50,22 52,29 46,25 40,29 42,22 36,17 43,17"/><path d="M2 12h28M8 20h22M14 28h16M90 12H62M84 20H62M78 28H62"/></svg>
  <h3>Pilot &amp; Emerging Tech Support</h3>
  <p>Lorem ipsum dolor sit amet, consectetur adipiscing elit, sed do eiusmod tempor incididunt ut labore et dolore magna aliqua.</p>
  <a class="more">Read More</a>
</article>

<article class="service" style="left:440px;top:1390px">
  <svg class="icon" width="48" height="50" viewBox="0 0 48 50" fill="none" stroke="#111" stroke-width="2" style="top:-25px"><rect x="2" y="30" width="6" height="18"/><rect x="12" y="24" width="6" height="24"/><rect x="22" y="20" width="6" height="28"/><rect x="32" y="14" width="6" height="34"/><polyline points="2,24 14,16 26,18 44,2"/></svg>
  <h3>Program Portfolio &amp; Resource Planning</h3>
  <p>Lorem ipsum dolor sit amet, consectetur adipiscing elit, sed do eiusmod tempor incididunt ut labore et dolore magna aliqua.</p>
  <a class="more">Read More</a>
</article>

<article class="service" style="left:779px;top:1390px">
  <svg class="icon" width="96" height="54" viewBox="0 0 96 54" fill="none" stroke="#111" stroke-width="2" style="top:-24px"><rect x="26" y="2" width="44" height="36"/><path d="M70 14h14l10 14v10H70"/><circle cx="40" cy="44" r="6"/><circle cx="82" cy="44" r="6"/><path d="M2 12h20M8 22h14M2 32h20"/></svg>
  <h3>Program Delivery Support</h3>
  <p>Lorem ipsum dolor sit amet, consectetur adipiscing elit, sed do eiusmod tempor incididunt ut labore et dolore magna aliqua.</p>
  <a class="more">Read More</a>
</article>

<div class="cases-band"></div>
<h2 class="section-title cases-title">Case Studies</h2>

<article class="case" style="left:98px">
  <div class="case-media" role="img" aria-label="Photo of hands holding a glowing cloud icon surrounded by data network graphics" style="background:linear-gradient(135deg,#1c3558,#2e5580 50%,#9a6a4a 70%,#1a2e4d)"></div>
  <h3>Journal Articles and Conference Presentations</h3>
  <a class="btn">Learn More</a>
</article>

<article class="case" style="left:619px">
  <div class="case-media" role="img" aria-label="Photo of a laptop showing charts on an office desk beside coffee cups" style="background:linear-gradient(135deg,#dfe3e2,#c9ccc8 45%,#6f7574 70%,#b7bab6)"></div>
  <h3>Published Reports</h3>
  <a class="btn">Learn More</a>
</article>

<a class="view-all">View All Case Studies</a>

<footer class="site-footer">
  <div class="rule"></div>
  <a class="brand" style="left:100px;top:2514px"><span class="brand-dot"></span><span class="brand-name">Harrow Point Metrics</span></a>
  <nav class="top-nav" style="left:544px;top:2523px">
    <a>Home</a><a>Core Services</a><a>About</a><a>Our Work</a><a>Blog</a><a>Contact Us</a>
  </nav>
  <p class="copyright">Copyright © 2022 Harrow Point Metrics</p>
</footer>

</body>
</html>
```